Start up Dialysis Clinic needs its first website - Velmira Health

Create a visually appealing and user-friendly website for Velmira Health, a dialysis clinic located in Mt. Irvine, Tobago. The website should effectively communicate our services to local, regional, and international patients, providing essential information and fostering trust and engagement..
Key Goals:

1. Informative: Provide comprehensive information about our services, facility, and team.
2. User-Friendly: Ensure the website is easy to navigate, with a clear structure and accessible content.
3. Engaging: Create a visually appealing design that reflects the professionalism and care of Velmira Health.
4. Responsive: Ensure the website is fully responsive and performs well on all devices, including desktops, tablets, and smartphones.
5. Trust-Building: Include testimonials, credentials, and patient resources to build trust with potential patients.
Scope of Work:

1. Home Page: An inviting and informative landing page that provides an overview of our clinic, mission, and services. Include a call to action for more information and contact details.
2. About Us: A detailed page about Velmira Health, including our mission, vision, team, and facility tour.
3. Services: A comprehensive page describing the dialysis services we offer, including Hemodialysis, Peritoneal Dialysis, and Home Hemodialysis.
4. Patient Information: A resourceful section with guides for new patients, FAQs, insurance and billing information, and downloadable forms.
5. Resources: Educational content about kidney health, dialysis options, diet and nutrition tips, and support groups.
6. Contact Us: A contact page with our address, phone number, email, office hours, a contact form, and a map.

```html
<!DOCTYPE html>
<html lang="en">
<head>
<meta charset="utf-8">
<title>Velmira Health – Dialysis Care in Mt. Irvine, Tobago</title>
<link rel="stylesheet" href="https://fonts.googleapis.com/css2?family=Montserrat:wght@600;700;800&family=Roboto:wght@400;500;700&display=swap">
<style>
:root{
  --blue:#1d6db3;
  --blue-dark:#134b82;
  --green:#2f8f5a;
  --green-dark:#1f6e45;
  --teal:#2a8c86;
  --navy:#0c2638;
  --ink:#3a4652;
  --muted:#6d7884;
  --white:#ffffff;
  --line:#c9d3dc;
}
*{box-sizing:border-box;margin:0;padding:0}
html,body{width:1200px;height:3572px;overflow:hidden;background:#fff}
body{font-family:"Roboto",Arial,sans-serif;color:var(--ink)}
.page{position:relative;width:1200px;height:3572px;overflow:hidden}
.abs{position:absolute}
h1,h2,h3{font-family:"Montserrat",Arial,sans-serif}

/* header */
.topbar{top:0;left:0;width:1200px;height:112px;background:#fff;border-bottom:4px solid var(--green)}
.contact-mini{top:14px;right:40px;display:flex;gap:40px;font-size:14px;color:var(--ink)}
.contact-mini span{display:flex;align-items:center;gap:8px}
.contact-mini i{display:inline-block;width:18px;height:18px;background:var(--green);border-radius:3px}
.nav{top:60px;left:470px;display:flex;gap:34px;font-size:15px;font-weight:500;color:#1c2a36;text-transform:uppercase}
.nav a{color:inherit;text-decoration:none;padding-bottom:6px}
.nav a.active{border-bottom:2px solid var(--green)}
.logo-box{top:0;left:140px;width:160px;height:152px;background:#fff;z-index:5;display:flex;flex-direction:column;align-items:center;justify-content:center;gap:10px;box-shadow:0 4px 10px rgba(0,0,0,.12)}
.logo-mark{width:46px;height:46px;background:var(--blue)}
.logo-name{font-family:"Montserrat",Arial,sans-serif;font-weight:800;font-size:20px;color:var(--blue);text-align:center;line-height:1.1}

/* hero */
.hero{top:112px;left:0;width:1200px;height:470px;background:radial-gradient(circle at 50% 35%,#3d8fc6 0%,#1d5e93 45%,#0e3559 100%);clip-path:polygon(0 0,100% 0,100% 86%,0 100%)}
.hero-title{top:232px;width:1200px;text-align:center;color:#fff;font-size:54px;font-weight:800;letter-spacing:1px}
.hero-sub{top:302px;width:1200px;text-align:center;color:#fff;font-size:18px;font-weight:700}
.btn{display:inline-block;background:var(--blue);color:#fff;font-family:"Montserrat",Arial,sans-serif;font-weight:700;font-size:14px;text-transform:uppercase;padding:14px 24px;letter-spacing:.5px}
.btn-ghost{background:var(--green);border:2px solid #fff}
.hero-btn{top:350px;left:525px}
.dots{top:396px;right:56px;display:flex;flex-direction:column;gap:10px}
.dots i{width:8px;height:8px;border-radius:50%;background:#fff;display:block}

/* overview */
.overview-frame{top:628px;left:168px;width:348px;height:368px;border:4px solid var(--green)}
.overview-photo{top:640px;left:180px;width:324px;height:344px;background:linear-gradient(135deg,#2f8f5a 0%,#dfe9ef 45%,#1d6db3 100%)}
.sec-title{font-size:52px;font-weight:800;color:var(--blue);letter-spacing:1px}
.overview-title{top:618px;left:590px}
.overview-rule{top:690px;left:590px;width:450px;height:2px;background:var(--green)}
.overview-text{top:714px;left:590px;width:450px;font-size:15px;line-height:1.75;color:var(--muted)}
.overview-btn{top:912px;left:590px}

/* mission */
.mission{top:1012px;left:0;width:1200px;height:380px;background:linear-gradient(100deg,var(--green) 0%,var(--teal) 55%,var(--blue) 100%);clip-path:polygon(0 14%,100% 0,100% 86%,0 100%)}
.mission-title{top:1146px;left:200px;color:#fff;font-size:44px;font-weight:800;line-height:1.15}
.mission-rule{top:1150px;left:470px;width:2px;height:120px;background:rgba(255,255,255,.6)}
.mission-text{top:1148px;left:494px;width:480px;color:#fff;font-size:15px;line-height:1.7}
.mission-btn{top:1278px;left:494px}

/* services */
.services-title{top:1464px;width:1200px;text-align:center}
.card{top:1580px;width:284px;height:336px;background:#fff;border:5px solid var(--green);text-align:center;padding:30px 26px}
.card.featured{top:1568px;height:362px;background:var(--blue);border-color:var(--blue-dark);color:#fff}
.card-icon{width:56px;height:56px;margin:0 auto 16px;border:3px solid var(--blue);border-radius:50%}
.card.featured .card-icon{border-color:#fff}
.card h3{font-size:18px;font-weight:700;text-transform:uppercase;margin-bottom:12px;color:#1c2a36}
.card.featured h3{color:#fff}
.card p{font-size:14px;line-height:1.65;color:var(--muted);margin-bottom:20px}
.card.featured p{color:#e4eef7}
.card .btn{padding:11px 20px;font-size:13px}
.card.featured .btn{background:#fff;color:var(--blue)}
.card-1{left:148px}
.card-2{left:460px}
.card-3{left:772px}

/* testimonials */
.testimonials{top:1900px;left:0;width:1200px;height:560px;background:linear-gradient(160deg,#2e9a62 0%,#1f7a4c 45%,#5da6c7 100%);clip-path:polygon(0 18%,100% 0,100% 100%,0 100%)}
.test-title{top:2092px;width:1200px;text-align:center;color:#fff;font-size:52px;font-weight:800}
.quote-mark{top:2190px;left:582px}
.test-text{top:2250px;left:250px;width:700px;text-align:center;color:#fff;font-size:17px;font-style:italic;line-height:1.6}
.test-name{top:2358px;width:1200px;text-align:center;color:#fff;font-weight:700;font-size:18px}
.arrow{top:2290px}
.arrow-l{left:140px}
.arrow-r{right:140px}

/* contact */
.contact-bg{top:2440px;left:0;width:1200px;height:900px;background:linear-gradient(180deg,#eaf1f6 0%,#c9d9e6 55%,#6d8191 100%)}
.contact-panel{top:2470px;left:140px;width:920px;height:850px;background:rgba(255,255,255,.92)}
.contact-title{top:2580px;width:1200px;text-align:center}
.info{top:2680px;width:280px;text-align:center;font-size:16px;color:#1c2a36;line-height:1.5}
.info-icon{width:92px;height:92px;border-radius:50%;background:var(--green);border:6px solid #d3e7da;margin:0 auto 14px;display:flex;align-items:center;justify-content:center}
.info-1{left:150px}
.info-2{left:460px}
.info-3{left:770px}
.form{top:2960px;left:215px;width:770px}
.row{display:flex;gap:170px;margin-bottom:22px}
.field{flex:1;height:40px;border:1px solid var(--line);border-radius:20px;padding:0 22px;font-size:13px;color:var(--muted);display:flex;align-items:center;background:#fff}
.field.area{height:90px;align-items:flex-start;padding-top:12px;border-radius:20px}
.submit{top:3210px;left:512px}

/* footer */
.footer{top:3340px;left:0;width:1200px;height:232px;background:var(--navy);border-top:6px solid var(--green)}
.foot-logo{top:3378px;left:140px;display:flex;flex-direction:column;align-items:center;gap:10px}
.foot-logo .logo-name{color:#fff}
.foot-logo .logo-mark{background:var(--green)}
.social{top:3374px;left:410px;display:flex;gap:14px}
.social i{display:block;width:40px;height:40px;border-radius:50%;background:#fff}
.foot-nav{top:3460px;left:410px;display:flex;gap:40px;color:#fff;font-size:15px;font-weight:500;text-transform:uppercase}
.foot-rule{top:3500px;left:410px;width:650px;height:1px;background:rgba(255,255,255,.3)}
.copy{top:3518px;left:410px;color:#b6c3cf;font-size:13px}
</style>
</head>
<body>
<div class="page">

  <header>
    <div class="abs topbar"></div>
    <div class="abs contact-mini">
      <span><i></i>+1 868 555 0142</span>
      <span><i></i>info@velmirahealth.com</span>
    </div>
    <nav class="abs nav">
      <a class="active" href="#">Home</a><a href="#">About Us</a><a href="#">Patient Information</a><a href="#">Resources</a><a href="#">Contact Us</a>
    </nav>
    <div class="abs logo-box"><span class="logo-mark"></span><span class="logo-name">VELMIRA<br>HEALTH</span></div>
  </header>

  <section>
    <div class="abs hero" role="img" aria-label="Blue medical image of kidneys with a patient in the background"></div>
    <h1 class="abs hero-title">VELMIRA HEALTH</h1>
    <p class="abs hero-sub">Caring dialysis treatment in Mt. Irvine, Tobago</p>
    <a class="abs btn btn-ghost hero-btn">Get Started</a>
    <div class="abs dots"><i></i><i></i><i></i></div>
  </section>

  <section>
    <div class="abs overview-frame"></div>
    <div class="abs overview-photo" role="img" aria-label="Nurse caring for a patient in a bright clinic room"></div>
    <h2 class="abs sec-title overview-title">OVERVIEW</h2>
    <div class="abs overview-rule"></div>
    <p class="abs overview-text">Velmira Health offers calm, modern dialysis care in Mt. Irvine, Tobago. Our nurses and doctors guide each patient through treatment with patience, clear answers and steady support. We welcome local, regional and visiting patients, and we plan every session around your health, your schedule and your comfort.</p>
    <a class="abs btn overview-btn">Read More</a>
  </section>

  <section>
    <div class="abs mission"></div>
    <h2 class="abs mission-title">OUR<br>MISSION</h2>
    <div class="abs mission-rule"></div>
    <p class="abs mission-text">Our mission is to give every patient safe, dignified dialysis close to home, with kind staff, clean rooms and honest advice that helps people live fuller lives.</p>
    <a class="abs btn btn-ghost mission-btn">Read More</a>
  </section>

  <section>
    <h2 class="abs sec-title services-title">OUR SERVICES</h2>
    <div class="abs card card-1"><div class="card-icon"></div><h3>Hemodialysis</h3><p>Treatment in our clinic with skilled nurses watching every session from start to finish.</p><a class="btn">Read More</a></div>
    <div class="abs card featured card-2"><div class="card-icon"></div><h3>Peritoneal Dialysis</h3><p>A gentle home option that uses the lining of the belly to clean the blood.</p><a class="btn">Read More</a></div>
    <div class="abs card card-3"><div class="card-icon"></div><h3>Home Hemodialysis</h3><p>Dialysis in your own home, with training and support from our care team.</p><a class="btn">Read More</a></div>
  </section>

  <section>
    <div class="abs testimonials" role="img" aria-label="Green outdoor scene of a happy patient on a grassy hill"></div>
    <h2 class="abs test-title">TESTIMONIALS</h2>
    <svg class="abs quote-mark" width="36" height="36" viewBox="0 0 36 36"><path d="M3 30V18Q3 6 15 4v5q-6 2-6 9h6v12zM21 30V18q0-12 12-14v5q-6 2-6 9h6v12z" fill="none" stroke="#fff" stroke-width="2"/></svg>
    <p class="abs test-text">"The team made my first weeks on dialysis far easier than I feared. Every nurse knew my name, explained each step, and made the clinic feel like a second home for my whole family."</p>
    <p class="abs test-name">- Renata Cole</p>
    <svg class="abs arrow arrow-l" width="24" height="44" viewBox="0 0 24 44"><path d="M20 2 4 22l16 20" fill="none" stroke="#fff" stroke-width="3"/></svg>
    <svg class="abs arrow arrow-r" width="24" height="44" viewBox="0 0 24 44"><path d="M4 2l16 20L4 42" fill="none" stroke="#fff" stroke-width="3"/></svg>
  </section>

  <section>
    <div class="abs contact-bg" role="img" aria-label="Hillside town with mountains under a pale sky"></div>
    <div class="abs contact-panel"></div>
    <h2 class="abs sec-title contact-title">CONTACT US</h2>
    <div class="abs info info-1">
      <div class="info-icon"><svg width="38" height="38" viewBox="0 0 24 24"><path d="M6.6 10.8a15 15 0 0 0 6.6 6.6l2.2-2.2a1 1 0 0 1 1-.25 11 11 0 0 0 3.6.6 1 1 0 0 1 1 1V20a1 1 0 0 1-1 1A17 17 0 0 1 3 4a1 1 0 0 1 1-1h3.5a1 1 0 0 1 1 1 11 11 0 0 0 .6 3.6 1 1 0 0 1-.25 1z" fill="#fff"/></svg></div>
      Phone<br>+1 868 555 0142
    </div>
    <div class="abs info info-2">
      <div class="info-icon"><svg width="38" height="38" viewBox="0 0 24 24"><path d="M12 2a7 7 0 0 0-7 7c0 5 7 13 7 13s7-8 7-13a7 7 0 0 0-7-7zm0 9.5A2.5 2.5 0 1 1 12 6.5a2.5 2.5 0 0 1 0 5z" fill="#fff"/></svg></div>
      Mt. Irvine Road, Mt. Irvine,<br>Tobago
    </div>
    <div class="abs info info-3">
      <div class="info-icon"><svg width="38" height="38" viewBox="0 0 24 24"><path d="M3 5h18v14H3z" fill="#fff"/><path d="M3 5l9 7 9-7" fill="none" stroke="#2f8f5a" stroke-width="1.6"/></svg></div>
      Email<br>info@velmirahealth.com
    </div>
    <form class="abs form">
      <div class="row"><div class="field">Enter Name</div><div class="field">Enter Email</div></div>
      <div class="row"><div class="field">Phone</div><div class="field">Address</div></div>
      <div class="row"><div class="field area">Message</div></div>
    </form>
    <a class="abs btn submit">Submit Message</a>
  </section>

  <footer>
    <div class="abs footer"></div>
    <div class="abs foot-logo"><span class="logo-mark"></span><span class="logo-name">VELMIRA<br>HEALTH</span></div>
    <div class="abs social"><i></i><i></i><i></i><i></i></div>
    <div class="abs foot-nav"><span>Home</span><span>About Us</span><span>Patient Information</span><span>Resources</span><span>Contact Us</span></div>
    <div class="abs foot-rule"></div>
    <p class="abs copy">© 2024 Velmira Health. All rights reserved | Privacy | Terms of Use</p>
  </footer>

</div>
</body>
</html>
```